Create American style design suitable for consumers in Europe and America

We need a professional universal neutral design, which can be applied to all personal care tools, regardless of male and female, and the color matching needs to be matched by designers themselves.
Updates

设计质量低

Target Market(s)

Europe and America

Industry/Entity Type

personal care tools

Font styles to use
Serif
Sans Serif
Script

Requirements
Must have
• personal beauty care tool,like nail clipper,tweezer,scissors
Nice to have
• The copywriter plans on the packaging design can be applied to all personal care tools
Should not have
• Not designed for a single product, but for a whole personal care tool

```html
<!DOCTYPE html>
<html lang="en">
<head>
<meta charset="utf-8">
<title>Arlo Care – Nail Clipper Packaging Card</title>
<link href="https://fonts.googleapis.com/css2?family=Jost:wght@300;400&family=Great+Vibes&family=Oswald:wght@600&family=Montserrat:wght@700&display=swap" rel="stylesheet">
<style>
  :root {
    --stage: #cccccc;
    --card-dark: #060606;
    --card-mid: #1c1c1c;
    --ink: #ffffff;
    --badge-ink: #1a1a1a;
    --badge-fill: #ffffff;
  }
  * { margin: 0; padding: 0; box-sizing: border-box; }
  html, body { width: 1200px; height: 999px; overflow: hidden; background: var(--stage); }
  .canvas { position: relative; width: 1200px; height: 999px; }

  .card {
    position: absolute; top: 75px; width: 508px; height: 849px;
    border-radius: 24px; overflow: hidden;
    background: radial-gradient(ellipse at 35% 55%, var(--card-mid) 0%, var(--card-dark) 70%);
    color: var(--ink); text-align: center;
  }
  .card--front { left: 73px; }
  .card--back { left: 615px; }

  .hang-hole { position: absolute; left: 50%; top: 28px; transform: translateX(-50%); }

  .brand {
    position: absolute; left: 0; right: 0; top: 112px;
    font-family: "Jost", sans-serif; font-weight: 400;
    font-size: 44px; letter-spacing: 1px; line-height: 1;
  }

  .product-photo {
    position: absolute; left: 76px; top: 194px; width: 348px; height: 508px;
    border-radius: 16px;
    background: radial-gradient(ellipse at 50% 45%, #3a3a3a 0%, #151515 60%, rgba(6,6,6,0) 100%);
  }

  .title {
    font-family: "Jost", sans-serif; font-weight: 400;
    font-size: 63px; line-height: 1; letter-spacing: 0.5px;
    position: absolute; left: 0; right: 0;
  }
  .card--front .title { top: 712px; }
  .card--back .title { top: 208px; }

  .tagline {
    font-family: "Great Vibes", cursive; font-size: 36px; line-height: 1;
    position: absolute; left: 0; right: 0;
  }
  .card--front .tagline { top: 778px; }
  .card--back .tagline { top: 275px; }

  .description {
    position: absolute; left: 48px; width: 405px; top: 334px;
    font-family: "Jost", sans-serif; font-weight: 300;
    font-size: 14.2px; line-height: 22.3px;
    text-align: justify; text-align-last: center;
  }

  .badges { position: absolute; top: 578px; left: 0; right: 0; display: flex; justify-content: center; gap: 28px; }
  .badge {
    width: 106px; height: 106px; border-radius: 50%; background: var(--badge-fill);
    display: flex; align-items: center; justify-content: center;
    color: var(--badge-ink);
    font-family: "Oswald", sans-serif; font-weight: 600; font-size: 15.5px; line-height: 19px;
    position: relative;
  }
  .badge::after {
    content: ""; position: absolute; inset: 5px; border-radius: 50%;
    border: 1.5px solid var(--badge-ink);
  }

  .contact {
    position: absolute; left: 0; right: 0; top: 708px;
    font-family: "Montserrat", sans-serif; font-weight: 700;
    font-size: 17.5px; line-height: 26px;
  }
</style>
</head>
<body>
<div class="canvas">

  <section class="card card--front">
    <svg class="hang-hole" width="120" height="50" viewBox="0 0 120 50" aria-hidden="true">
      <circle cx="60" cy="15" r="15" fill="var(--stage)"/>
      <rect x="1" y="14" width="118" height="28" rx="14" fill="var(--stage)"/>
    </svg>
    <div class="brand">Arlo Care</div>
    <div class="product-photo" role="img" aria-label="Photo of a stainless steel cuticle nipper with black speckled handles"></div>
    <h1 class="title">NAIL CLIPPER</h1>
    <p class="tagline">Personal beauty care tool</p>
  </section>

  <section class="card card--back">
    <svg class="hang-hole" width="120" height="50" viewBox="0 0 120 50" aria-hidden="true">
      <circle cx="60" cy="15" r="15" fill="var(--stage)"/>
      <rect x="1" y="14" width="118" height="28" rx="14" fill="var(--stage)"/>
    </svg>
    <div class="brand">Arlo Care</div>
    <h2 class="title">NAIL CLIPPER</h2>
    <p class="tagline">Personal beauty care tool</p>
    <p class="description">Lorem Ipsum is simply dummy text of the printing and type-setting industry. Lorem Ipsum has been the industry's standard dummy text ever since the 1500s, when an unknown printer took a galley of type and scrambled it to make a type specimen book. It has survived not only five centuries, but also the leap into electronic typesetting, remaining essentially unchanged. It was popularised in the 1960s with the release of Letraset sheets containing Lorem Ipsum passages, and more recently with desktop publishing software like Aldus PageMaker including versions of Lorem Ipsum.</p>
    <div class="badges">
      <div class="badge">High<br>Quality<br>Stainless<br>Steel</div>
      <div class="badge">100%<br>Satisfaction<br>Guatanteed</div>
    </div>
    <div class="contact">
      ANY QUESTIONS? CONTACT US<br>
      PH: (123) 456-7890<br>
      E: contact@emailaddress.com<br>
      W: www.websiteaddress.com
    </div>
  </section>

</div>
</body>
</html>
```